Mobile Friendly Lead Generation Landing Page

We are a web marketing company that specialized in web lead generation. Recently we have started buying media from mobile devices and we need a mobile interface(landing page) where we can collect user data in an effective manner.

Our current mobile landing page is:
http://www.tutorpath.example.com/lp13d/index.aspx?a=true&source=841356
Through this you can see what the steps/questions users need to answer to get matched to a school. We need the design for the whole process.

We are pretty open for design ideas and our goal is to make this mobile optimized landing page have the look and feel of an app...but not an app.
There are several questions in the process but we are open to changing the way they are presented. As in, you can have one question at a time or a few.
The goal is to make this EXTREMELY EASY for users to interact with.

One example that we have liked is:
http://learnvane.example/schools/57214-page1.lvne (please note that this opens only on mobile devices)

Some of these screenshots are attached.

Our web form looks like this:
http://www.tutorpath.example.com/lp88/index.aspx?a=true

```html
<!DOCTYPE html>
<html lang="en">
<head>
<meta charset="utf-8">
<title>Main Screen Revisions</title>
<link href="https://fonts.googleapis.com/css2?family=Roboto:wght@300;400;500;700&family=Roboto+Condensed:wght@400&display=swap" rel="stylesheet">
<style>
  :root {
    --page-bg: #eef4f1;
    --sky: #149af2;
    --url-field: #8ed2fa;
    --stripe: #c6e6f6;
    --banner: #bfe2f3;
    --headline: #1a7be6;
    --ribbon: #f6c318;
    --ribbon-dark: #e2a90c;
    --header-red: #ef1316;
    --row-line: #dedede;
    --row-text: #222;
    --go-green: #1ebd1e;
    --toolbar: #0b63f2;
    --caption: #2b2b2b;
    --ic-art: #f0127a;
    --ic-business: #17c21a;
    --ic-justice: #ee1416;
    --ic-edu: #1468f0;
    --ic-eng: #f97a10;
    --ic-other: #111;
  }
  * { box-sizing: border-box; margin: 0; padding: 0; }
  html, body { width: 1200px; height: 840px; overflow: hidden; }
  body { background: var(--page-bg); position: relative; font-family: "Roboto", sans-serif; }

  .screen { position: absolute; top: 132px; width: 300px; height: 533px; background: #fff; overflow: hidden; box-shadow: 0 2px 10px rgba(0,0,0,.12); }
  .screen--rev1 { left: 212px; }
  .screen--rev11 { left: 671px; }

  .browser-top { height: 60px; background: var(--sky); color: #fff; }
  .status-bar { height: 20px; display: flex; align-items: center; justify-content: space-between; padding: 0 8px; font-size: 11px; }
  .status-bar .signal { letter-spacing: -1px; margin-right: 3px; }
  .battery { display: inline-block; width: 22px; height: 9px; border: 1px solid #fff; vertical-align: middle; margin-left: 3px; background: #fff; }
  .url-field { margin: 6px 10px 0; height: 26px; border-radius: 5px; background: var(--url-field); display: flex; align-items: center; justify-content: center; position: relative; font-size: 15px; }
  .url-field svg { position: absolute; right: 8px; top: 5px; }

  .stripe { height: 15px; background: var(--stripe); }
  .intro { height: 41px; display: flex; align-items: center; justify-content: center; font-size: 18px; font-weight: 300; color: var(--headline); }
  .intro strong { font-weight: 700; margin: 0 4px; }

  .grant-banner { height: 83px; background: var(--banner); position: relative; }
  .grant-banner svg { position: absolute; left: 0; top: 0; }
  .grant-text { position: absolute; left: 55px; width: 190px; top: 24px; text-align: center; color: #fff; font-size: 11.5px; line-height: 17px; font-weight: 400; }

  .section-header { height: 40px; background: var(--header-red); color: #fff; font-family: "Roboto Condensed", sans-serif; font-size: 16.5px; display: flex; align-items: center; justify-content: center; }

  .interest-list { list-style: none; }
  .interest { height: 41.2px; border-bottom: 1px solid var(--row-line); display: flex; align-items: center; padding: 0 10px 0 6px; font-family: "Roboto Condensed", sans-serif; font-size: 14px; color: var(--row-text); }
  .interest:last-child { border-bottom: none; }
  .interest-icon { width: 31px; height: 31px; border-radius: 50%; display: flex; align-items: center; justify-content: center; margin-right: 9px; }
  .screen--rev11 .interest-icon { border-radius: 6px; }
  .interest-name { flex: 1; }
  .icon-art { background: var(--ic-art); } .icon-business { background: var(--ic-business); }
  .icon-justice { background: var(--ic-justice); } .icon-edu { background: var(--ic-edu); }
  .icon-eng { background: var(--ic-eng); } .icon-other { background: var(--ic-other); }

  .toolbar { position: absolute; bottom: 0; left: 0; right: 0; height: 47px; background: var(--toolbar); display: flex; align-items: center; justify-content: space-around; }

  .caption { position: absolute; top: 784px; width: 400px; text-align: center; font-size: 29px; font-weight: 300; color: var(--caption); }
  .caption--rev1 { left: 162px; }
  .caption--rev11 { left: 621px; }
</style>
</head>
<body>

<!-- Revision 1 -->
<section class="screen screen--rev1">
  <div class="browser-top">
    <div class="status-bar"><span><span class="signal">●●●○○</span> Nimbus</span><span>4:21 PM</span><span>100%<span class="battery"></span></span></div>
    <div class="url-field">www.tutorpath.example.com
      <svg width="16" height="16" viewBox="0 0 16 16"><path d="M13 8a5 5 0 1 1-2-4" fill="none" stroke="#fff" stroke-width="1.5"/><path d="M11 1v3.5h3.5" fill="none" stroke="#fff" stroke-width="1.5"/></svg>
    </div>
  </div>
  <div class="stripe"></div>
  <p class="intro">Complete our <strong>3 minute</strong> App!</p>
  <div class="grant-banner">
    <svg width="300" height="83" viewBox="0 0 300 83">
      <polygon points="18,28 60,28 60,58 18,58 30,43" fill="var(--ribbon-dark)"/>
      <polygon points="282,28 240,28 240,58 282,58 270,43" fill="var(--ribbon-dark)"/>
      <polyline points="28,36 38,43 28,50" fill="none" stroke="#fff" stroke-width="1.5"/>
      <polyline points="272,36 262,43 272,50" fill="none" stroke="#fff" stroke-width="1.5"/>
      <rect x="50" y="10" width="200" height="62" rx="6" fill="var(--ribbon)"/>
      <rect x="57" y="17" width="186" height="48" rx="3" fill="none" stroke="#fff" stroke-width="1.5" stroke-dasharray="4 3"/>
    </svg>
    <p class="grant-text">Get up to $5, 645* per year<br>in Grants if you qualify</p>
  </div>
  <h2 class="section-header">SELECT AREA OF YOUR INTEREST</h2>
  <ul class="interest-list">
    <li class="interest"><span class="interest-icon icon-art"><svg width="18" height="18" viewBox="0 0 18 18"><path d="M15 2L7 11M6 11c-2 0-3 2-3 5 3 0 5-1 5-3z" fill="none" stroke="#fff" stroke-width="1.3"/></svg></span><span class="interest-name">Art &amp; Design</span><svg width="20" height="20" viewBox="0 0 20 20"><circle cx="10" cy="10" r="10" fill="var(--go-green)"/><polyline points="8,5.5 12.5,10 8,14.5" fill="none" stroke="#fff" stroke-width="2.2"/></svg></li>
    <li class="interest"><span class="interest-icon icon-business"><svg width="20" height="18" viewBox="0 0 20 18"><rect x="2" y="5" width="16" height="11" fill="none" stroke="#fff" stroke-width="1.3"/><path d="M7 5V2h6v3M2 9h16M9 9v2h2V9" fill="none" stroke="#fff" stroke-width="1.3"/></svg></span><span class="interest-name">Business</span><svg width="20" height="20" viewBox="0 0 20 20"><circle cx="10" cy="10" r="10" fill="var(--go-green)"/><polyline points="8,5.5 12.5,10 8,14.5" fill="none" stroke="#fff" stroke-width="2.2"/></svg></li>
    <li class="interest"><span class="interest-icon icon-justice"><svg width="20" height="20" viewBox="0 0 20 20"><rect x="3" y="4" width="9" height="5" transform="rotate(-35 7 6)" fill="#fff"/><path d="M9 9l7 6" stroke="#fff" stroke-width="2"/><rect x="2" y="16" width="9" height="2" fill="#fff"/></svg></span><span class="interest-name">Criminal Justice</span><svg width="20" height="20" viewBox="0 0 20 20"><circle cx="10" cy="10" r="10" fill="var(--go-green)"/><polyline points="8,5.5 12.5,10 8,14.5" fill="none" stroke="#fff" stroke-width="2.2"/></svg></li>
    <li class="interest"><span class="interest-icon icon-edu"><svg width="24" height="22" viewBox="0 0 24 22"><text x="12" y="9" font-size="8.5" fill="#fff" text-anchor="middle" font-family="Roboto, sans-serif">ABC</text><line x1="3" y1="11" x2="21" y2="11" stroke="#fff" stroke-width=".8"/><text x="12" y="19" font-size="8.5" fill="#fff" text-anchor="middle" font-family="Roboto, sans-serif">1 2 3</text></svg></span><span class="interest-name">Education &amp; Teaching</span><svg width="20" height="20" viewBox="0 0 20 20"><circle cx="10" cy="10" r="10" fill="var(--go-green)"/><polyline points="8,5.5 12.5,10 8,14.5" fill="none" stroke="#fff" stroke-width="2.2"/></svg></li>
    <li class="interest"><span class="interest-icon icon-eng"><svg width="20" height="20" viewBox="0 0 20 20"><circle cx="10" cy="3.5" r="1.8" fill="none" stroke="#fff" stroke-width="1.2"/><path d="M9 5L4 18M11 5l5 13M5 13h10" fill="none" stroke="#fff" stroke-width="1.3"/></svg></span><span class="interest-name">Engineering</span><svg width="20" height="20" viewBox="0 0 20 20"><circle cx="10" cy="10" r="10" fill="var(--go-green)"/><polyline points="8,5.5 12.5,10 8,14.5" fill="none" stroke="#fff" stroke-width="2.2"/></svg></li>
    <li class="interest"><span class="interest-icon icon-other"><svg width="20" height="18" viewBox="0 0 20 18"><path d="M10 4C7 2 4 2 2 3v12c2-1 5-1 8 1 3-2 6-2 8-1V3c-2-1-5-1-8 1zM10 4v12" fill="none" stroke="#fff" stroke-width="1.3"/></svg></span><span class="interest-name">Other</span><svg width="20" height="20" viewBox="0 0 20 20"><circle cx="10" cy="10" r="10" fill="var(--go-green)"/><polyline points="8,5.5 12.5,10 8,14.5" fill="none" stroke="#fff" stroke-width="2.2"/></svg></li>
  </ul>
  <nav class="toolbar">
    <svg width="16" height="22" viewBox="0 0 16 22"><polyline points="12,2 3,11 12,20" fill="none" stroke="#fff" stroke-width="1.6"/></svg>
    <svg width="16" height="22" viewBox="0 0 16 22"><polyline points="4,2 13,11 4,20" fill="none" stroke="#fff" stroke-width="1.6"/></svg>
    <svg width="22" height="24" viewBox="0 0 22 24"><path d="M7 8H3v14h16V8h-4M11 15V2M7 6l4-4 4 4" fill="none" stroke="#fff" stroke-width="1.4"/></svg>
    <svg width="26" height="22" viewBox="0 0 26 22"><path d="M13 4C9 2 5 2 2 3v16c3-1 7-1 11 1 4-2 8-2 11-1V3c-3-1-7-1-11 1zM13 4v16" fill="none" stroke="#fff" stroke-width="1.4"/></svg>
    <svg width="28" height="22" viewBox="0 0 28 22"><rect x="2" y="6" width="20" height="14" fill="none" stroke="#fff" stroke-width="1.4"/><path d="M6 6V2h20v14h-4" fill="none" stroke="#fff" stroke-width="1.4"/></svg>
  </nav>
</section>

<!-- Revision 1.1 -->
<section class="screen screen--rev11">
  <div class="browser-top">
    <div class="status-bar"><span><span class="signal">●●●○○</span> Nimbus</span><span>4:21 PM</span><span>100%<span class="battery"></span></span></div>
    <div class="url-field">www.tutorpath.example.com
      <svg width="16" height="16" viewBox="0 0 16 16"><path d="M13 8a5 5 0 1 1-2-4" fill="none" stroke="#fff" stroke-width="1.5"/><path d="M11 1v3.5h3.5" fill="none" stroke="#fff" stroke-width="1.5"/></svg>
    </div>
  </div>
  <div class="stripe"></div>
  <p class="intro">Complete our <strong>3 minute</strong> App!</p>
  <div class="grant-banner">
    <svg width="300" height="83" viewBox="0 0 300 83">
      <polygon points="18,28 60,28 60,58 18,58 30,43" fill="var(--ribbon-dark)"/>
      <polygon points="282,28 240,28 240,58 282,58 270,43" fill="var(--ribbon-dark)"/>
      <polyline points="28,36 38,43 28,50" fill="none" stroke="#fff" stroke-width="1.5"/>
      <polyline points="272,36 262,43 272,50" fill="none" stroke="#fff" stroke-width="1.5"/>
      <rect x="50" y="10" width="200" height="62" rx="6" fill="var(--ribbon)"/>
      <rect x="57" y="17" width="186" height="48" rx="3" fill="none" stroke="#fff" stroke-width="1.5" stroke-dasharray="4 3"/>
    </svg>
    <p class="grant-text">Get up to $5, 645* per year<br>in Grants if you qualify</p>
  </div>
  <h2 class="section-header">SELECT AREA OF YOUR INTEREST</h2>
  <ul class="interest-list">
    <li class="interest"><span class="interest-icon icon-art"><svg width="18" height="18" viewBox="0 0 18 18"><path d="M15 2L7 11M6 11c-2 0-3 2-3 5 3 0 5-1 5-3z" fill="none" stroke="#fff" stroke-width="1.3"/></svg></span><span class="interest-name">Art &amp; Design</span><svg width="20" height="20" viewBox="0 0 20 20"><circle cx="10" cy="10" r="10" fill="var(--go-green)"/><polyline points="8,5.5 12.5,10 8,14.5" fill="none" stroke="#fff" stroke-width="2.2"/></svg></li>
    <li class="interest"><span class="interest-icon icon-business"><svg width="20" height="18" viewBox="0 0 20 18"><rect x="2" y="5" width="16" height="11" fill="none" stroke="#fff" stroke-width="1.3"/><path d="M7 5V2h6v3M2 9h16M9 9v2h2V9" fill="none" stroke="#fff" stroke-width="1.3"/></svg></span><span class="interest-name">Business</span><svg width="20" height="20" viewBox="0 0 20 20"><circle cx="10" cy="10" r="10" fill="var(--go-green)"/><polyline points="8,5.5 12.5,10 8,14.5" fill="none" stroke="#fff" stroke-width="2.2"/></svg></li>
    <li class="interest"><span class="interest-icon icon-justice"><svg width="20" height="20" viewBox="0 0 20 20"><rect x="3" y="4" width="9" height="5" transform="rotate(-35 7 6)" fill="#fff"/><path d="M9 9l7 6" stroke="#fff" stroke-width="2"/><rect x="2" y="16" width="9" height="2" fill="#fff"/></svg></span><span class="interest-name">Criminal Justice</span><svg width="20" height="20" viewBox="0 0 20 20"><circle cx="10" cy="10" r="10" fill="var(--go-green)"/><polyline points="8,5.5 12.5,10 8,14.5" fill="none" stroke="#fff" stroke-width="2.2"/></svg></li>
    <li class="interest"><span class="interest-icon icon-edu"><svg width="24" height="22" viewBox="0 0 24 22"><text x="12" y="9" font-size="8.5" fill="#fff" text-anchor="middle" font-family="Roboto, sans-serif">ABC</text><line x1="3" y1="11" x2="21" y2="11" stroke="#fff" stroke-width=".8"/><text x="12" y="19" font-size="8.5" fill="#fff" text-anchor="middle" font-family="Roboto, sans-serif">1 2 3</text></svg></span><span class="interest-name">Education &amp; Teaching</span><svg width="20" height="20" viewBox="0 0 20 20"><circle cx="10" cy="10" r="10" fill="var(--go-green)"/><polyline points="8,5.5 12.5,10 8,14.5" fill="none" stroke="#fff" stroke-width="2.2"/></svg></li>
    <li class="interest"><span class="interest-icon icon-eng"><svg width="20" height="20" viewBox="0 0 20 20"><circle cx="10" cy="3.5" r="1.8" fill="none" stroke="#fff" stroke-width="1.2"/><path d="M9 5L4 18M11 5l5 13M5 13h10" fill="none" stroke="#fff" stroke-width="1.3"/></svg></span><span class="interest-name">Engineering</span><svg width="20" height="20" viewBox="0 0 20 20"><circle cx="10" cy="10" r="10" fill="var(--go-green)"/><polyline points="8,5.5 12.5,10 8,14.5" fill="none" stroke="#fff" stroke-width="2.2"/></svg></li>
    <li class="interest"><span class="interest-icon icon-other"><svg width="20" height="18" viewBox="0 0 20 18"><path d="M10 4C7 2 4 2 2 3v12c2-1 5-1 8 1 3-2 6-2 8-1V3c-2-1-5-1-8 1zM10 4v12" fill="none" stroke="#fff" stroke-width="1.3"/></svg></span><span class="interest-name">Other</span><svg width="20" height="20" viewBox="0 0 20 20"><circle cx="10" cy="10" r="10" fill="var(--go-green)"/><polyline points="8,5.5 12.5,10 8,14.5" fill="none" stroke="#fff" stroke-width="2.2"/></svg></li>
  </ul>
  <nav class="toolbar">
    <svg width="16" height="22" viewBox="0 0 16 22"><polyline points="12,2 3,11 12,20" fill="none" stroke="#fff" stroke-width="1.6"/></svg>
    <svg width="16" height="22" viewBox="0 0 16 22"><polyline points="4,2 13,11 4,20" fill="none" stroke="#fff" stroke-width="1.6"/></svg>
    <svg width="22" height="24" viewBox="0 0 22 24"><path d="M7 8H3v14h16V8h-4M11 15V2M7 6l4-4 4 4" fill="none" stroke="#fff" stroke-width="1.4"/></svg>
    <svg width="26" height="22" viewBox="0 0 26 22"><path d="M13 4C9 2 5 2 2 3v16c3-1 7-1 11 1 4-2 8-2 11-1V3c-3-1-7-1-11 1zM13 4v16" fill="none" stroke="#fff" stroke-width="1.4"/></svg>
    <svg width="28" height="22" viewBox="0 0 28 22"><rect x="2" y="6" width="20" height="14" fill="none" stroke="#fff" stroke-width="1.4"/><path d="M6 6V2h20v14h-4" fill="none" stroke="#fff" stroke-width="1.4"/></svg>
  </nav>
</section>

<p class="caption caption--rev1">Main Screen Revision 1</p>
<p class="caption caption--rev11">Main Screen Revision 1.1</p>

</body>
</html>
```